Im want a website LIKE VRX's and FleetHollow.com's with product payment options like Trenzo's

I need a website LIKE VRX with a header made EXACTLY LIKE THAT OF FLEETHOLLOWS .

The front page photo should be like that of FLEETHOLLOW's webpage as well.

The name of the website will be called "M.K. (Caldera Key)".

We will be targeting ALL MARKETS in a small town in central Panama and charging businesses "listing fees" like a phone book does but also providing informational blogs, news, and other interesting activities.

THIS IS A MULTI PAGE WEBSITE

THIS IS WHERE VRX's website meets Brivelle/FleetHollow.

Once the layout is built I will tweak and modify, add information, and upload items for sale.

Here is a list of specific categories that should be listed out above the front page header image/search bar

-- Home -- News -- Travel -- Activities -- Shop & Dine -- Store -- More... --

These categories should be spread across the bottom of the page in three sections:

WHATS SO GREAT ABOUT (Caldera Key),
HAND PICKED TOURS
ACTIVITIES etc.

Also lets use www.Trenzo.example 's
"HOT DESTINATIONS"
"BEAT THE BEST PRICES IN BOQUETE"
"OCTOBERS INSIDER PICKS"
"TOP DESTINATIONS"
and spread them in four sections side-by-side near the bottom of the page.

Overall I would like to see the finished product to be something LIKE VRX's and FleetHollows.

WE NEED ONLINE PAYMENT OPTIONS LIKE BRIVELLE'S WEBSITE HAS

This will be a desktop website but should be very mobile friendly as well.

-rodmund

P.S. Good luck!

If it isn't already too late to change the website name, the name of the website should be "Caldera Key". Added Friday, October 9, 2015

What do you guys think the budget should be to win this? Added Saturday, October 10, 2015

www.palmorra.example is the most amazing simple site. Whoever can make me a replica with my specifications will win immediately!!!! Added Sunday, October 18, 2015

OMG www.palmorra.example is the bomb!So simple and elegant. Whoever can make me an EXACT REPLICA OF WWW.PALMORRA.EXAMPLE as my site with the specifications mentioned in my brief will take home the $825.00 immediately! Good luck amigos! Added Sunday, October 18, 2015

Does anybody know how to add recurring monthly billing options on this website? Added Sunday, October 18, 2015

ALL MARKETS

Product

Coded - Design and coding required

5+ page

• Coinvey payment options.
• I must be able to add and remove photos/text and video from the HTML files in the page.
• Be creative my friends, and may the odds be forever in your favor!
• I added some photos of a good layout for our page below.

```html
<!DOCTYPE html>
<html lang="en">
<head>
<meta charset="utf-8">
<title>Caldera Key</title>
<link href="https://fonts.googleapis.com/css2?family=Open+Sans:wght@400;600;700&family=Raleway:wght@500;600;700;800&display=swap" rel="stylesheet">
<style>
:root{
  --blue:#2b79bb;
  --blue-dark:#1f5f95;
  --ink:#33404a;
  --muted:#8a949c;
  --line:#d9dee2;
  --gray-bg:#eef1f3;
  --white:#ffffff;
  --footer:#232b31;
  --footer-2:#1b2227;
  --footer-text:#aab3ba;
  --star:#f2b01e;
}
*{box-sizing:border-box;margin:0;padding:0}
html,body{width:1200px;height:2592px;overflow:hidden}
body{font-family:"Open Sans",Arial,sans-serif;color:var(--ink);background:var(--white);position:relative}
.abs{position:absolute}

/* header + hero */
.hero{position:absolute;left:0;top:0;width:1200px;height:612px;
  background:linear-gradient(180deg,#4f9fd0 0%,#7cc0e2 35%,#5fb8cf 55%,#3e95b4 70%,#d7d2c0 88%,#e6e1d2 100%)}
.topbar{position:absolute;left:0;top:0;width:1200px;height:78px;background:rgba(255,255,255,.94)}
.lang{position:absolute;right:70px;top:6px;font-size:12px;color:var(--muted);display:flex;gap:22px}
.nav{position:absolute;top:40px;font-family:"Raleway",sans-serif;font-weight:700;font-size:14px;color:var(--ink);display:flex;gap:48px;letter-spacing:.3px}
.nav.left{left:96px}.nav.right{left:724px}
.nav .active{color:var(--blue)}
.logo{position:absolute;left:530px;top:0;width:140px;height:110px;background:var(--white);border-radius:0 0 70px 70px;text-align:center;padding-top:30px}
.logo .mark{display:block;width:22px;height:22px;border-radius:50%;background:var(--blue);margin:0 auto 6px}
.logo .name{font-family:"Raleway",sans-serif;font-weight:800;font-size:17px;color:var(--blue);line-height:1.1}

.slider{position:absolute;left:162px;top:250px;width:872px;height:352px;background:var(--white);box-shadow:0 8px 24px rgba(0,0,0,.2);padding:28px}
.slider-photo{position:absolute;left:28px;top:28px;width:400px;height:290px;background:linear-gradient(160deg,#8fd1ee 0%,#47b6c8 45%,#1e8ca5 70%,#2a6a86 100%)}
.slider-text{position:absolute;left:462px;top:36px;width:380px}
.slider-title{display:flex;align-items:center;gap:14px;font-family:"Raleway",sans-serif;font-weight:700;font-size:26px;color:var(--blue)}
.slider-title::after{content:"";flex:1;height:2px;background:var(--blue)}
.slider-text p{font-size:12.5px;line-height:22px;color:var(--muted);margin-top:18px}
.btn{display:inline-block;background:var(--blue);color:var(--white);font-family:"Raleway",sans-serif;font-weight:700;font-size:12px;letter-spacing:.6px;padding:9px 18px;border-radius:3px}
.slider .btn{margin-top:18px}
.dots{position:absolute;left:574px;top:316px;display:flex;gap:8px}
.dots i{width:8px;height:8px;border-radius:50%;background:#cfd5d9}
.dots i.on{background:var(--blue)}

/* why choose */
.why{position:absolute;left:0;top:612px;width:1200px;height:708px;background:var(--gray-bg)}
.sec-title{font-family:"Raleway",sans-serif;font-weight:800;font-size:24px;color:var(--blue-dark);letter-spacing:.5px}
.why .sec-title{position:absolute;left:96px;top:200px}
.why .sec-title::after{content:"";display:inline-block;width:120px;height:2px;background:var(--blue);margin-left:18px;vertical-align:middle}
.feature{position:absolute;width:300px;display:flex;gap:18px}
.feature .ico{flex:none;width:42px;height:42px;border-radius:50%;background:var(--blue);display:flex;align-items:center;justify-content:center}
.feature h3{font-family:"Raleway",sans-serif;font-weight:700;font-size:16px;color:var(--ink);margin-top:4px}
.feature p{font-size:12px;line-height:20px;color:var(--muted);margin-top:6px;width:210px}

.search{position:absolute;left:768px;top:176px;width:320px;height:440px;background:var(--blue);padding:18px 18px}
.search h2{font-family:"Raleway",sans-serif;font-weight:700;font-size:22px;color:var(--white);text-align:center}
.tabs{display:flex;gap:4px;margin-top:14px}
.tabs span{flex:1;font-size:11px;text-align:center;padding:6px 0;background:rgba(255,255,255,.25);color:var(--white)}
.tabs span.on{background:var(--white);color:var(--blue)}
.field{display:flex;align-items:center;margin-top:12px;height:36px;background:var(--white)}
.field .fi{width:36px;height:36px;border-right:1px solid var(--line);display:flex;align-items:center;justify-content:center}
.field span{font-size:12px;color:var(--muted);padding-left:12px}
.search .btn{display:block;width:150px;margin:18px auto 0;text-align:center;background:var(--blue-dark)}

/* tours */
.center-title{position:absolute;left:0;width:1200px;display:flex;justify-content:center;align-items:center;gap:26px}
.center-title .rule{width:150px;height:2px;background:var(--blue);position:relative}
.center-title .rule.l::before,.center-title .rule.r::after{content:"";position:absolute;top:-3px;width:8px;height:8px;border-radius:50%;background:var(--blue)}
.center-title .rule.l::before{left:0}.center-title .rule.r::after{right:0}
.card{position:absolute;top:1388px;width:284px;height:346px;background:var(--white);box-shadow:0 3px 14px rgba(0,0,0,.14)}
.card-photo{height:204px;position:relative}
.tag{position:absolute;left:10px;top:10px;background:var(--blue);color:var(--white);font-size:10px;padding:3px 8px}
.price{position:absolute;right:0;bottom:0;background:var(--blue);color:var(--white);font-weight:700;font-size:13px;padding:5px 12px}
.card-body{padding:14px 18px}
.card h3{font-family:"Raleway",sans-serif;font-weight:700;font-size:16px;color:var(--ink)}
.card p{font-size:11.5px;line-height:18px;color:var(--muted);margin-top:8px}
.card-foot{position:absolute;left:0;bottom:0;width:100%;height:44px;border-top:1px solid var(--line);display:flex;align-items:center;padding:0 16px;font-size:11px;color:var(--muted);gap:8px}
.stars{color:var(--star);letter-spacing:1px;margin-left:28px}
.card-foot .go{margin-left:auto}
.arrow-btn{position:absolute;top:1592px;width:32px;height:32px;border:1px solid var(--line);border-radius:50%;background:var(--white);display:flex;align-items:center;justify-content:center}

/* great about */
.band{position:absolute;left:0;top:1940px;width:1200px;height:262px;background:linear-gradient(180deg,#3a86a8 0%,#2f7394 55%,#245d7a 100%)}
.perk{position:absolute;top:26px;width:200px;text-align:center;color:var(--white)}
.perk h4{font-family:"Raleway",sans-serif;font-weight:700;font-size:16px;letter-spacing:.6px}
.perk .circle{width:66px;height:66px;border-radius:50%;border:2px solid var(--white);margin:36px auto 0;display:flex;align-items:center;justify-content:center}
.perk .ghost{display:inline-block;margin-top:18px;border:1px solid rgba(255,255,255,.8);font-size:10px;font-weight:600;letter-spacing:.6px;padding:6px 14px;border-radius:3px}

/* footer */
.footer{position:absolute;left:0;top:2202px;width:1200px;height:390px;background:var(--footer);color:var(--footer-text)}
.footer h5{font-family:"Raleway",sans-serif;font-weight:700;font-size:14px;color:var(--white);letter-spacing:.5px}
.footer ul{list-style:none;margin-top:14px;font-size:12px;line-height:22px}
.footer p{font-size:11.5px;line-height:19px;margin-top:14px}
.news-form{display:flex;margin-top:12px;width:340px}
.news-form span{flex:1;height:30px;background:var(--white)}
.news-form .btn{border-radius:0;padding:8px 16px;font-size:11px}
.social{position:absolute;left:96px;top:250px;display:flex;gap:76px;font-size:12px}
.social span{display:flex;align-items:center;gap:10px}
.social i{width:16px;height:16px;border-radius:50%;background:#5c6870;display:inline-block}
.program{position:absolute;left:910px;top:242px;border:1px solid #6d777e;padding:7px 16px;font-size:12px;color:var(--white);display:flex;align-items:center;gap:8px}
.program i{width:10px;height:10px;background:#6d777e;display:inline-block}
.copy{position:absolute;left:0;top:320px;width:1200px;height:70px;background:var(--footer-2);text-align:center;font-size:11px;padding-top:22px}
</style>
</head>
<body>

<header class="hero">
  <div class="abs" style="inset:0" role="img" aria-label="Tropical beach with palm trees, turquoise sea and sky"></div>
  <div class="topbar">
    <div class="lang"><span>English ▾</span><span>USD ▾</span></div>
    <nav class="nav left"><span class="active">HOME</span><span>TOURS</span><span>TICKETS</span><span>TOUR GUIDES</span></nav>
    <nav class="nav right"><span>HOTELS</span><span>PLACES</span><span>BLOG</span><span>CONTACT US</span></nav>
  </div>
  <div class="logo"><span class="mark"></span><span class="name">Caldera<br>Key</span></div>

  <section class="slider">
    <div class="slider-photo" role="img" aria-label="Long-tail boat moored in clear turquoise water by limestone cliffs"></div>
    <div class="slider-text">
      <h2 class="slider-title">Caldera Key</h2>
      <p>Pellentesque in ipsum id orci porta dapibus. Vivamus magna justo, lacinia eget consectetur sed, convallis at tellus. Vestibulum ac diam sit amet quam vehicula elementum sed sit amet dui. Donec sollicitudin molestie malesuada. Curabitur aliquet quam id dui posuere blandit.</p>
      <p style="margin-top:10px">Nulla quis lorem ut libero malesuada feugiat. Proin eget tortor risus, sed porttitor lectus nibh.</p>
      <span class="btn">CONTACT US</span>
    </div>
    <div class="dots"><i class="on"></i><i></i><i></i></div>
  </section>
</header>

<section class="why">
  <h2 class="sec-title">WHY CHOOSE US?</h2>

  <div class="feature" style="left:96px;top:290px">
    <span class="ico"><svg width="20" height="20" viewBox="0 0 20 20"><circle cx="10" cy="10" r="8" fill="none" stroke="#fff" stroke-width="2"/><path d="M2 10h16M10 2c3 3 3 13 0 16M10 2c-3 3-3 13 0 16" fill="none" stroke="#fff" stroke-width="1.5"/></svg></span>
    <div><h3>Diverse destinations</h3><p>Vestibulum ante ipsum primis in faucibus orci luctus et ultrices posuere.</p></div>
  </div>
  <div class="feature" style="left:416px;top:290px">
    <span class="ico"><svg width="20" height="20" viewBox="0 0 20 20"><circle cx="10" cy="7" r="4" fill="#fff"/><path d="M3 18c0-4 3-6 7-6s7 2 7 6z" fill="#fff"/></svg></span>
    <div><h3>Instant help</h3><p>Vestibulum ante ipsum primis in faucibus orci luctus et ultrices posuere.</p></div>
  </div>
  <div class="feature" style="left:96px;top:440px">
    <span class="ico"><svg width="20" height="20" viewBox="0 0 20 20"><rect x="3" y="4" width="14" height="13" rx="1" fill="none" stroke="#fff" stroke-width="2"/><path d="M3 8h14M7 2v4M13 2v4" stroke="#fff" stroke-width="2"/></svg></span>
    <div><h3>Fast booking</h3><p>Vestibulum ante ipsum primis in faucibus orci luctus et ultrices posuere.</p></div>
  </div>
  <div class="feature" style="left:416px;top:440px">
    <span class="ico"><svg width="20" height="20" viewBox="0 0 20 20"><path d="M3 3h7l8 8-7 7-8-8z" fill="#fff"/><circle cx="7" cy="7" r="1.6" fill="#2b79bb"/></svg></span>
    <div><h3>Best prices</h3><p>Vestibulum ante ipsum primis in faucibus orci luctus et ultrices posuere.</p></div>
  </div>

  <form class="search">
    <h2>Search Tours</h2>
    <div class="tabs"><span class="on">Guided Tours</span><span>Hotel Rooms</span><span>Special Offers</span></div>
    <div class="field"><span class="fi"><svg width="14" height="14" viewBox="0 0 14 14"><circle cx="6" cy="6" r="4.5" fill="none" stroke="#2b79bb" stroke-width="1.6"/><path d="M9.5 9.5L13 13" stroke="#2b79bb" stroke-width="1.6"/></svg></span><span>Search Key</span></div>
    <div class="field"><span class="fi"><svg width="12" height="14" viewBox="0 0 12 14"><path d="M6 13S1 8 1 5a5 5 0 0110 0c0 3-5 8-5 8z" fill="#2b79bb"/><circle cx="6" cy="5" r="1.8" fill="#fff"/></svg></span><span>Destination</span></div>
    <div class="field"><span class="fi"><svg width="14" height="14" viewBox="0 0 14 14"><path d="M2 4h10M2 7h10M2 10h10" stroke="#2b79bb" stroke-width="1.6"/></svg></span><span>Tour Type</span></div>
    <div class="field"><span class="fi"><svg width="14" height="14" viewBox="0 0 14 14"><rect x="1.5" y="2.5" width="11" height="10" fill="none" stroke="#2b79bb" stroke-width="1.4"/><path d="M1.5 5.5h11" stroke="#2b79bb" stroke-width="1.4"/></svg></span><span>Date</span></div>
    <div class="field"><span class="fi"><svg width="14" height="14" viewBox="0 0 14 14"><circle cx="7" cy="7" r="5.5" fill="none" stroke="#2b79bb" stroke-width="1.4"/><path d="M7 4v3l2 2" stroke="#2b79bb" stroke-width="1.4" fill="none"/></svg></span><span>Month</span></div>
    <span class="btn">SEARCH TOUR</span>
  </form>
</section>

<section>
  <div class="center-title" style="top:1316px"><span class="rule l"></span><h2 class="sec-title">MOST POPULAR TOURS</h2><span class="rule r"></span></div>

  <span class="arrow-btn" style="left:28px"><svg width="10" height="12" viewBox="0 0 10 12"><path d="M7 1L2 6l5 5" fill="none" stroke="#8a949c" stroke-width="2"/></svg></span>
  <span class="arrow-btn" style="left:1140px"><svg width="10" height="12" viewBox="0 0 10 12"><path d="M3 1l5 5-5 5" fill="none" stroke="#8a949c" stroke-width="2"/></svg></span>

  <article class="card" style="left:108px">
    <div class="card-photo" role="img" aria-label="Palm tree silhouette on a beach at golden sunset" style="background:linear-gradient(180deg,#f6b640 0%,#f3d27a 45%,#3a9fc0 75%,#e9dcb6 100%)"><span class="tag">Last Deals</span><span class="price">$ 100</span></div>
    <div class="card-body"><h3>Voluptatem Sequi</h3><p>Lorem ipsum dolor sit amet, consectetur adipiscing elit nulla facilisi sed do eiusmod tempor.</p></div>
    <div class="card-foot"><span>◷ 10 hours</span><span class="stars">★★★☆☆</span><span class="go"><svg width="14" height="10" viewBox="0 0 14 10"><path d="M0 5h12M8 1l4 4-4 4" fill="none" stroke="#2b79bb" stroke-width="2"/></svg></span></div>
  </article>
  <article class="card" style="left:458px">
    <div class="card-photo" role="img" aria-label="Colourful boats moored at a tropical harbour" style="background:linear-gradient(180deg,#9fd0ea 0%,#6fb4d4 40%,#3b8aa6 70%,#6a8a7c 100%)"><span class="price">$ 100</span></div>
    <div class="card-body"><h3>Voluptatem Sequi</h3><p>Lorem ipsum dolor sit amet, consectetur adipiscing elit nulla facilisi sed do eiusmod tempor.</p></div>
    <div class="card-foot"><span>◷ 10 hours</span><span class="stars">★★★☆☆</span><span class="go"><svg width="14" height="10" viewBox="0 0 14 10"><path d="M0 5h12M8 1l4 4-4 4" fill="none" stroke="#2b79bb" stroke-width="2"/></svg></span></div>
  </article>
  <article class="card" style="left:808px">
    <div class="card-photo" role="img" aria-label="Wooden long-tail boat resting on clear shallow water" style="background:linear-gradient(180deg,#a9d8ef 0%,#62c0d8 45%,#2aa0b4 70%,#c69a5c 100%)"><span class="tag">Last Deals</span><span class="price">$ 100</span></div>
    <div class="card-body"><h3>Voluptatem Sequi</h3><p>Lorem ipsum dolor sit amet, consectetur adipiscing elit nulla facilisi sed do eiusmod tempor.</p></div>
    <div class="card-foot"><span>◷ 10 hours</span><span class="stars">★★★☆☆</span><span class="go"><svg width="14" height="10" viewBox="0 0 14 10"><path d="M0 5h12M8 1l4 4-4 4" fill="none" stroke="#2b79bb" stroke-width="2"/></svg></span></div>
  </article>
</section>

<section>
  <div class="center-title" style="top:1862px"><span class="rule l"></span><h2 class="sec-title">GREAT ABOUT CALDERA KEY</h2><span class="rule r"></span></div>
  <div class="band" role="img" aria-label="Palm trees over a turquoise lagoon in soft blue tones">
    <div class="perk" style="left:100px"><h4>24/7 SUPPORT</h4>
      <div class="circle"><svg width="30" height="28" viewBox="0 0 30 28"><path d="M3 3h24v16H12l-6 6v-6H3z" fill="none" stroke="#fff" stroke-width="2"/></svg></div>
      <span class="ghost">WITH A LIVE PERSON</span></div>
    <div class="perk" style="left:370px"><h4>VERIFIED</h4>
      <div class="circle"><svg width="30" height="26" viewBox="0 0 30 26"><rect x="2" y="6" width="26" height="18" rx="2" fill="none" stroke="#fff" stroke-width="2"/><circle cx="15" cy="15" r="5" fill="none" stroke="#fff" stroke-width="2"/><path d="M10 6l2-4h6l2 4" fill="none" stroke="#fff" stroke-width="2"/></svg></div>
      <span class="ghost">VERIFIED PHOTOS</span></div>
    <div class="perk" style="left:640px"><h4>VIP PERSON</h4>
      <div class="circle"><svg width="26" height="28" viewBox="0 0 26 28"><circle cx="13" cy="8" r="6" fill="none" stroke="#fff" stroke-width="2"/><path d="M2 27c0-7 5-11 11-11s11 4 11 11" fill="none" stroke="#fff" stroke-width="2"/></svg></div>
      <span class="ghost">WITH A LIVE PERSON</span></div>
    <div class="perk" style="left:910px"><h4>LOW PRICES</h4>
      <div class="circle"><svg width="28" height="28" viewBox="0 0 28 28"><path d="M3 3h11l11 11-11 11L3 14z" fill="none" stroke="#fff" stroke-width="2"/><circle cx="9" cy="9" r="2" fill="#fff"/></svg></div>
      <span class="ghost">WITH A LIVE PERSON</span></div>
  </div>
</section>

<footer class="footer">
  <div class="abs" style="left:96px;top:50px">
    <h5>LEARN MORE</h5>
    <ul><li>About Us</li><li>FAQ</li><li>Work with Us</li><li>Press</li></ul>
  </div>
  <div class="abs" style="left:320px;top:50px;width:300px">
    <h5>FROM THE BLOG</h5>
    <p>Nullam quis risus eget urna mollis ornare vel eu leo. Cras mattis consectetur purus sit amet fermentum. Donec ullamcorper nulla non metus auctor fringilla. Maecenas sed diam eget risus varius.</p>
  </div>
  <div class="abs" style="left:688px;top:40px;width:420px">
    <h5 style="font-size:17px">NEWSLETTER SUBSCRIPTION</h5>
    <p>Sign up for our newsletter and get the latest tour offers and travel news delivered straight to your inbox every week.</p>
    <div class="news-form"><span></span><span class="btn">SUBSCRIBE</span></div>
  </div>
  <div class="social"><span><i></i>Friendlane</span><span><i></i>Circlet Plus</span><span><i></i>Chirpwave</span><span><i></i>Linkora</span></div>
  <span class="program"><i></i>Partner Program</span>
  <div class="copy">© Copyright Caldera Key. All Rights Reserved.</div>
</footer>

</body>
</html>
```